Accounting business needs business card

I have a business card but need something better. I want the colour changed and the design to be better. I have uploaded a picture of my new sign that is grey in colour, i would like to incorporate these colours.

```html
<!DOCTYPE html>
<html lang="en">
<head>
<meta charset="utf-8">
<title>LEVELTAX business card</title>
<link href="https://fonts.googleapis.com/css2?family=Montserrat:wght@400;500;700&display=swap" rel="stylesheet">
<style>
  :root {
    --stage: #2a2a2c;
    --card-dark: #2c2d31;
    --card-light: #ffffff;
    --ink: #1e1e20;
    --ink-soft: #3a3a3d;
    --on-dark: #ffffff;
    --badge-fill: #d6d7da;
  }
  * { box-sizing: border-box; margin: 0; padding: 0; }
  html, body { width: 1200px; height: 881px; overflow: hidden; }
  body {
    background: var(--stage);
    font-family: "Montserrat", sans-serif;
    position: relative;
  }
  .card {
    position: absolute;
    left: 290px;
    width: 620px;
    height: 354px;
    border-radius: 18px;
    box-shadow: 0 10px 30px rgba(0,0,0,.45);
    overflow: hidden;
  }
  .card-front { top: 46px; background: var(--card-dark); }
  .card-back  { top: 452px; background: var(--card-light); color: var(--ink); }

  /* front */
  .brand-mark {
    position: absolute;
    left: 50%; top: 74px;
    width: 118px; height: 118px;
    margin-left: -59px;
    border: 3px solid var(--on-dark);
    border-radius: 50%;
  }
  .brand-name {
    position: absolute;
    left: 0; right: 0; top: 226px;
    text-align: center;
    color: var(--on-dark);
    font-weight: 500;
    font-size: 40px;
    letter-spacing: 22px;
    padding-left: 22px;
  }

  /* back */
  .identity {
    position: absolute;
    left: 20px; top: 100px;
    width: 320px;
    text-align: right;
    white-space: nowrap;
  }
  .identity .person {
    font-weight: 700;
    font-size: 25px;
    letter-spacing: 2px;
    line-height: 1.1;
  }
  .identity .credentials,
  .identity .role {
    font-size: 13.5px;
    letter-spacing: 1.2px;
    color: var(--ink-soft);
    line-height: 1.35;
  }
  .divider {
    position: absolute;
    left: 358px; top: 96px;
    width: 1.5px; height: 76px;
    background: var(--ink);
  }
  .contacts {
    position: absolute;
    left: 376px; top: 98px;
    list-style: none;
    font-size: 13.5px;
    letter-spacing: .8px;
    line-height: 23px;
  }
  .contacts li { display: flex; align-items: center; gap: 8px; }
  .contacts svg { width: 12px; height: 12px; flex: none; }

  .badges {
    position: absolute;
    left: 176px; top: 214px;
    display: flex;
    align-items: flex-start;
    gap: 12px;
  }
  .badge-registered { width: 58px; text-align: center; }
  .badge-registered .seal {
    width: 54px; height: 54px; margin: 0 auto;
    border-radius: 50%;
    background: var(--badge-fill);
  }
  .badge-registered .agent-no {
    font-size: 7px; line-height: 1.15; margin-top: 3px;
  }
  .badge-software {
    width: 76px; height: 76px;
    border-radius: 50%;
    background: var(--badge-fill);
  }
  .badge-member {
    width: 180px; height: 88px;
    margin-top: -6px;
    background: var(--badge-fill);
  }
</style>
</head>
<body>

  <section class="card card-front" aria-label="Card front">
    <div class="brand-mark"></div>
    <div class="brand-name">LEVELTAX</div>
  </section>

  <section class="card card-back" aria-label="Card back">
    <div class="identity">
      <div class="person">DEAN WHITFORD</div>
      <div class="credentials">CPA, MTAX, BCOM (Acc &amp; Fin)</div>
      <div class="role">Taxation &amp; Business Accountant</div>
    </div>

    <div class="divider"></div>

    <ul class="contacts">
      <li>
        <svg viewBox="0 0 12 12" aria-hidden="true"><path d="M3 1 L5 3.5 L4 5 Q5 7 7 8 L8.5 7 L11 9 L9.5 11 Q4 10 1 3 Z" fill="none" stroke="#1e1e20" stroke-width="1.1"/></svg>
        0412 555 019
      </li>
      <li>
        <svg viewBox="0 0 12 12" aria-hidden="true"><rect x="1" y="2.5" width="10" height="7" fill="none" stroke="#1e1e20" stroke-width="1.1"/><path d="M1 2.5 L6 6.5 L11 2.5" fill="none" stroke="#1e1e20" stroke-width="1.1"/></svg>
        dean@leveltax.com.au
      </li>
      <li>
        <svg viewBox="0 0 12 12" aria-hidden="true"><circle cx="6" cy="6" r="5" fill="none" stroke="#1e1e20" stroke-width="1"/><ellipse cx="6" cy="6" rx="2.2" ry="5" fill="none" stroke="#1e1e20" stroke-width="1"/><path d="M1 6 H11 M2 3.5 H10 M2 8.5 H10" stroke="#1e1e20" stroke-width=".8"/></svg>
        www.leveltax.com.au
      </li>
    </ul>

    <div class="badges">
      <div class="badge-registered">
        <div class="seal" role="img" aria-label="Registered tax agent badge"></div>
        <div class="agent-no">Tax agent<br>12345678</div>
      </div>
      <div class="badge-software" role="img" aria-label="Accounting software partner badge"></div>
      <div class="badge-member" role="img" aria-label="Professional accounting body membership badge"></div>
    </div>
  </section>

</body>
</html>
```